KBT Business Cards

We require business cards for our business. We would like a matte black back to the card, with our logo centred in the middle. The front side of the card is open to design.

Target Market(s)

Clients looking for legal services (professional)

Industry/Entity Type

Legal

Contact Information for Business Card

Doran Kelbrath
Partner
Mobile: 0461 738 524
Email: doran@kbtlaw.co
Website: www.kbtlaw.co
Level 3, 118 Wendmore Street
Sydney NSW 2000

Font styles to use
Other font styles liked:
• Avenir

Colors
f04a50
ffffff
1b1b1b

Requirements
Must have
• Black back with logo included in the centre of the card.
• Our font is Avenir.

```html
<!DOCTYPE html>
<html lang="en">
<head>
<meta charset="utf-8">
<title>KBT Business Cards</title>
<link href="https://fonts.googleapis.com/css2?family=Nunito+Sans:wght@400;600;700&display=swap" rel="stylesheet">
<style>
  :root {
    --page: #2b2b2d;
    --card: #1b1b1b;
    --card-tint: #232323;
    --red: #d4204c;
    --white: #ffffff;
    --soft: #d9d9d9;
  }
  * { box-sizing: border-box; margin: 0; padding: 0; }
  html, body { width: 1200px; height: 800px; overflow: hidden; }
  body {
    background: var(--page);
    font-family: "Nunito Sans", "Avenir", sans-serif;
    color: var(--white);
    position: relative;
  }
  .card {
    position: absolute;
    top: 245px;
    width: 540px;
    height: 310px;
    border-radius: 22px;
    background: var(--card);
    overflow: hidden;
    box-shadow: 0 18px 40px rgba(0,0,0,.45);
  }
  .card--back { left: 40px; }
  .card--front { left: 620px; }

  /* back */
  .back-texture {
    position: absolute; inset: 0;
    background: linear-gradient(135deg, #202020 0%, #1b1b1b 55%, #171717 100%);
  }
  .back-mark {
    position: absolute; left: 50%; top: 50%;
    transform: translate(-50%, -50%);
    display: flex; align-items: center; gap: 10px;
  }
  .mark-square { width: 14px; height: 14px; background: var(--red); }
  .mark-name {
    font-weight: 700; font-size: 34px; letter-spacing: 4px; color: var(--white);
  }

  /* front */
  .front-glow {
    position: absolute; right: 0; top: 0; width: 260px; height: 170px;
    background: radial-gradient(ellipse at 70% 30%, #2f2f2f 0%, #262424 45%, rgba(27,27,27,0) 80%);
  }
  .firm {
    position: absolute; left: 34px; top: 40px;
    display: flex; align-items: center; gap: 14px;
  }
  .firm .mark-square { width: 18px; height: 18px; }
  .firm-name {
    font-weight: 700; font-size: 19px; line-height: 1.05;
    letter-spacing: .5px; text-transform: uppercase; color: var(--white);
  }
  .person { position: absolute; left: 34px; top: 128px; }
  .person-name {
    font-weight: 700; font-size: 17px; letter-spacing: .6px;
    text-transform: uppercase; color: var(--red);
  }
  .person-role { font-size: 14px; color: var(--soft); margin-top: 1px; }
  .address {
    position: absolute; right: 34px; top: 138px; text-align: right;
    font-size: 12.5px; line-height: 1.35; color: var(--soft);
  }
  .divider {
    position: absolute; left: 34px; right: 34px; top: 180px;
    height: 1.5px; background: var(--red);
  }
  .contacts {
    position: absolute; left: 34px; top: 196px;
    list-style: none; font-size: 14px; color: var(--white);
  }
  .contacts li { display: flex; align-items: center; gap: 10px; height: 24px; }
  .contacts svg { width: 13px; height: 13px; flex: none; }
</style>
</head>
<body>

<section class="card card--back" aria-label="Business card back">
  <div class="back-texture" role="img" aria-label="Matte black card back with faint tonal texture"></div>
  <div class="back-mark">
    <span class="mark-square"></span>
    <span class="mark-name">KBT</span>
  </div>
</section>

<section class="card card--front" aria-label="Business card front">
  <div class="front-glow" role="img" aria-label="Soft dark tonal decoration in the upper corner"></div>

  <div class="firm">
    <span class="mark-square"></span>
    <p class="firm-name">Kelbrath<br>Brandt<br>Legal</p>
  </div>

  <div class="person">
    <p class="person-name">Doran Kelbrath</p>
    <p class="person-role">Partner</p>
  </div>

  <p class="address">Level 3, 118 Wendmore Street<br>Sydney NSW 2000</p>

  <div class="divider"></div>

  <ul class="contacts">
    <li>
      <svg viewBox="0 0 13 13" aria-hidden="true"><rect x="1.5" y="1.5" width="10" height="10" fill="none" stroke="var(--red)" stroke-width="1.6"/></svg>
      0461 738 524
    </li>
    <li>
      <svg viewBox="0 0 13 13" aria-hidden="true"><rect x="0.5" y="2.5" width="12" height="8" fill="var(--red)"/><path d="M0.5 2.5 L6.5 7 L12.5 2.5" fill="none" stroke="var(--card)" stroke-width="1.2"/></svg>
      doran@kbtlaw.co
    </li>
    <li>
      <svg viewBox="0 0 13 13" aria-hidden="true"><circle cx="6.5" cy="6.5" r="5.5" fill="var(--red)"/><path d="M1 6.5 H12 M6.5 1 C3.5 4 3.5 9 6.5 12 M6.5 1 C9.5 4 9.5 9 6.5 12" fill="none" stroke="var(--card)" stroke-width="0.8"/></svg>
      www.kbtlaw.co
    </li>
  </ul>
</section>

</body>
</html>
```